BUSINESS CARD - HALLORAN FIELD SERVICES

I would like to create a business card for my fertilizer spreading business. I would like to incorporate my existing logo and also a description of the services offered. The business card will be given to farmers so must be kept simple but effective. It will also be left in stores so much also be eye catching in order to stand out from other cards.

Target Market(s)

FARMERS

Requirements
Must have
• FRONT OF CARD = EXISTING LOGO + "CUSTOMISED SPREADING" below the logo

REAR Of CARD = SERVICES OFFERED AND CONTACT DETAILS

- Bulk fertilizer including Lime, Gypsum, Manure & Compost
- Granular fertilizer including Single Super, Urea, Gran-am, & Custom Blends
- Modern equipment - Autosteer & Variable Rate Capable
- Friendly & Reliable Service
- Contact Gus: 0417 552 308
Nice to have
• utilize same color scheme as existing logo

```html
<!DOCTYPE html>
<html lang="en">
<head>
<meta charset="utf-8">
<title>Halloran Field Services – Business Card</title>
<link href="https://fonts.googleapis.com/css2?family=Open+Sans:wght@400;600;700&display=swap" rel="stylesheet">
<style>
  :root {
    --backdrop: #e4e4e4;
    --card: #f4f4f4;
    --charcoal: #555555;
    --orange: #f0922a;
    --text: #3c3c3c;
    --white: #ffffff;
  }
  * { box-sizing: border-box; margin: 0; padding: 0; }
  html, body { width: 1200px; height: 960px; overflow: hidden; }
  body {
    background: var(--backdrop);
    font-family: "Open Sans", Arial, sans-serif;
    position: relative;
  }
  .card {
    position: absolute;
    left: 319px;
    width: 569px;
    height: 348px;
    background: var(--card);
    overflow: hidden;
  }
  .card--front { top: 111px; }
  .card--back { top: 502px; height: 347px; }

  /* front */
  .brand-mark {
    position: absolute;
    left: 50%;
    top: 64px;
    width: 140px;
    height: 140px;
    margin-left: -70px;
    border-radius: 50%;
    background: var(--charcoal);
  }
  .brand-name {
    position: absolute;
    left: 0; right: 0;
    top: 220px;
    text-align: center;
    font-weight: 700;
    font-size: 30px;
    letter-spacing: 0.5px;
    color: var(--charcoal);
  }
  .tagline {
    position: absolute;
    left: 0; right: 0;
    top: 299px;
    text-align: center;
    font-weight: 700;
    font-size: 16.5px;
    letter-spacing: 1.2px;
    color: var(--charcoal);
  }
  .tagline .accent { color: var(--orange); }

  /* back */
  .scene-art {
    position: absolute;
    left: 0;
    top: 28px;
    width: 290px;
    height: 262px;
    background: linear-gradient(180deg, #ececec 0%, #dadada 100%);
  }
  .services {
    position: absolute;
    left: 329px;
    top: 42px;
    width: 230px;
    list-style: none;
  }
  .service { position: relative; padding-left: 18px; margin-bottom: 12px; }
  .service__icon {
    position: absolute;
    left: 0; top: 6px;
    width: 12px; height: 12px;
  }
  .service__title {
    font-weight: 700;
    font-size: 16px;
    line-height: 20.5px;
    color: var(--orange);
  }
  .service__detail {
    font-size: 15.5px;
    line-height: 20.5px;
    color: var(--text);
  }
  .contact-band {
    position: absolute;
    left: 0; right: 0; bottom: 0;
    height: 59px;
    background: var(--charcoal);
    display: flex;
    align-items: center;
    justify-content: center;
    gap: 8px;
  }
  .contact-band__rule {
    width: 142px;
    height: 2px;
    background: var(--orange);
  }
  .contact { display: flex; align-items: center; gap: 6px; margin: 0 8px; }
  .contact__name {
    font-weight: 700;
    font-size: 22px;
    letter-spacing: 0.5px;
    color: var(--orange);
  }
  .contact__icon { width: 18px; height: 18px; }
  .contact__phone {
    font-size: 17px;
    color: var(--white);
  }
</style>
</head>
<body>

  <section class="card card--front" aria-label="Card front">
    <div class="brand-mark" aria-hidden="true"></div>
    <h1 class="brand-name">HALLORAN FIELD SERVICES</h1>
    <p class="tagline"><span class="accent">CUSTOMISED</span> SPREADING</p>
  </section>

  <section class="card card--back" aria-label="Card back">
    <div class="scene-art" role="img" aria-label="Illustration of cattle and sheep grazing under an arching wheat stem"></div>

    <ul class="services">
      <li class="service">
        <svg class="service__icon" viewBox="0 0 12 12" aria-hidden="true"><circle cx="6" cy="6" r="5" fill="var(--orange)"/></svg>
        <div class="service__title">Bulk Fertilizer</div>
        <div class="service__detail">including Lime, Gypsum,<br>Manure &amp; Compost</div>
      </li>
      <li class="service">
        <svg class="service__icon" viewBox="0 0 12 12" aria-hidden="true"><circle cx="6" cy="6" r="5" fill="var(--orange)"/></svg>
        <div class="service__title">Granular Fertilizer</div>
        <div class="service__detail">including Single Super,<br>Urea, Gran-am<br>&amp; Custom Blends</div>
      </li>
      <li class="service">
        <svg class="service__icon" viewBox="0 0 12 12" aria-hidden="true"><circle cx="6" cy="6" r="5" fill="var(--orange)"/></svg>
        <div class="service__title">Modern Equipment</div>
        <div class="service__detail">Autosteer &amp; Variable<br>Rate Capable</div>
      </li>
    </ul>

    <footer class="contact-band">
      <span class="contact-band__rule"></span>
      <span class="contact">
        <span class="contact__name">GUS</span>
        <svg class="contact__icon" viewBox="0 0 20 20" aria-hidden="true">
          <circle cx="10" cy="10" r="8.6" fill="none" stroke="var(--orange)" stroke-width="1.6"/>
          <path d="M7 5.5l1.6 2.2-1 1.2c.6 1.3 1.5 2.2 2.8 2.8l1.2-1 2.2 1.6-.8 1.6c-3.6-.3-6.6-3.3-6.9-6.9z" fill="var(--orange)"/>
        </svg>
        <span class="contact__phone">0417 552 308</span>
      </span>
      <span class="contact-band__rule"></span>
    </footer>
  </section>

</body>
</html>
```